Brintle Hollowcraft web page for my social media pages

Need a web page designed around my logo and links to my social media pages that I can add an online merch store to in the future.
Similar to www.sketchbyatrolleycar.example
or
www.kelvatine.example
but dont require the picture background, just want a whit background with my log and name at the top and links to my social media underneath

Target Market(s)

Social media redirects and able to add merch store later

Industry/Entity Type

Manufacturing / repairs

Coding

Coded - Design and coding required

Number of Pages Required

1 page

Font styles to use
Other font styles liked:
• Similat to existing font for headings, body can be serif

Colors
0094D4
00A9DD
6FCCEA
C7EBF8
E9F6FB
FFF300
FFF600
FEFA6F
FFFEC7
FFFEE8
EB3D1F
EC4F4E
F09395
F8D3D4
FCEDEE

Requirements
Must have
• My logo and existing branding font/colours
Nice to have
• Like to be able to add merch at a later date
Should not have
• I do not have physical shop fornt or walk in customers

```html
<!DOCTYPE html>
<html lang="en">
<head>
<meta charset="utf-8">
<title>Brintle Hollowcraft</title>
<link rel="stylesheet" href="https://fonts.googleapis.com/css2?family=Bangers&family=Roboto:wght@400;500;700&display=swap">
<style>
:root{
  --black:#000000;
  --footer:#0b0b0b;
  --white:#ffffff;
  --cyan:#00f0f6;
  --yellow:#fff300;
  --red:#c8200f;
  --text:#555555;
  --ink:#111111;
}
*{box-sizing:border-box;margin:0;padding:0}
html,body{width:1200px;height:2466px;overflow:hidden;background:var(--white)}
body{position:relative;font-family:"Roboto",Arial,sans-serif;color:var(--text)}
.abs{position:absolute}
.hero{left:0;top:0;width:1200px;height:630px;background:var(--black);overflow:hidden}
.brand{left:144px;top:40px;display:flex;align-items:center;gap:12px}
.brand-mark{width:64px;height:64px;border-radius:50%;background:var(--cyan)}
.brand-name{font-family:"Roboto",Arial,sans-serif;font-weight:700;font-size:22px;color:var(--white);letter-spacing:.5px}
.menu{left:1028px;top:81px;width:28px;height:24px}
.menu span{display:block;height:4px;background:var(--white);margin-bottom:6px;border-radius:1px}
.hero-photo{left:595px;top:60px;width:480px;height:570px;border-radius:240px 240px 0 0;
  background:radial-gradient(circle at 50% 38%,#b3241a 0%,#6d1410 32%,#0d5d5d 55%,#000 78%),#000}
.hero-title{left:148px;top:263px;width:500px;font-family:"Bangers",cursive;font-size:66px;line-height:70px;color:var(--yellow);
  letter-spacing:0;text-shadow:-2px 0 var(--red),2px 0 var(--red),0 -2px var(--red),0 3px var(--red),3px 3px var(--red)}
.slider-dots{left:1126px;top:396px;width:8px}
.slider-dots i{display:block;width:7px;height:7px;border-radius:50%;background:var(--white);margin-bottom:9px}
.slider-dots i.active{background:var(--yellow)}
.btn{display:flex;align-items:center;justify-content:center;background:var(--cyan);color:var(--ink);
  font-family:"Roboto",Arial,sans-serif;font-weight:500;font-size:15px;border-radius:30px;letter-spacing:-.2px}
.btn-hero{left:148px;top:495px;width:147px;height:56px}
.btn-wide{width:275px;height:56px}
.media{width:461px;height:341px}
.media-road{background:linear-gradient(160deg,#8a8f9a 0%,#d89a4a 35%,#4b4640 65%,#2b2d33 100%)}
.media-dirt{background:linear-gradient(170deg,#a9b4b2 0%,#b79674 45%,#7a4d36 75%,#5a3b2a 100%)}
.media-curve{background:linear-gradient(180deg,#c9b27a 0%,#6f7a4a 40%,#4a4e47 70%,#8a8a86 100%)}
.arrow{position:absolute;top:146px;width:50px;height:47px;background:#111;display:flex;align-items:center;justify-content:center}
.arrow.prev{left:0}.arrow.next{right:0}
.play{position:absolute;left:203px;top:143px}
.section-title{font-family:"Bangers",cursive;font-size:50px;line-height:56px;color:var(--yellow);
  text-shadow:-2px 0 var(--red),2px 0 var(--red),0 -2px var(--red),0 3px var(--red),3px 3px var(--red);white-space:nowrap}
.copy{width:376px;font-size:16px;line-height:28.7px;text-align:justify;color:var(--text)}
.newsletter{left:0;top:2007px;width:1200px;height:334px;background:var(--black)}
.newsletter-title{left:0;width:1200px;top:2078px;text-align:center}
.newsletter-lead{left:0;width:1200px;top:2154px;text-align:center;color:var(--white);font-size:16px}
.email{left:334px;top:2213px;width:363px;height:56px;border-radius:30px;background:var(--white);
  color:var(--ink);font-size:14px;padding-left:42px;display:flex;align-items:center}
.btn-subscribe{left:703px;top:2213px;width:164px;height:56px;font-size:16px}
.footer{left:0;top:2341px;width:1200px;height:125px;background:var(--footer);border-top:1px solid #222}
.social{left:146px;top:2383px;display:flex;gap:6px}
.social a{width:44px;height:44px;border-radius:50%;background:var(--white);display:block}
.legal{right:146px;top:2393px;color:var(--white);font-size:14px}
</style>
</head>
<body>

<header class="abs hero">
  <div class="abs hero-photo" role="img" aria-label="Red sport motorcycle lit against a teal glow"></div>
  <div class="abs brand"><span class="brand-mark"></span><span class="brand-name">Brintle Hollowcraft</span></div>
  <div class="abs menu" aria-label="Menu"><span></span><span></span><span></span></div>
  <h1 class="abs hero-title">Adding adventures into an everyday life</h1>
  <a class="abs btn btn-hero">GET STARTED</a>
  <div class="abs slider-dots"><i></i><i class="active"></i><i></i></div>
</header>

<section>
  <div class="abs media media-road" style="left:147px;top:707px" role="img" aria-label="Rider on a cruiser motorcycle on an open road at sunset">
    <span class="arrow prev"><svg width="14" height="22" viewBox="0 0 14 22"><path d="M11 2 3 11l8 9" fill="none" stroke="#fff" stroke-width="2.5"/></svg></span>
    <svg class="play" width="56" height="56" viewBox="0 0 56 56"><circle cx="28" cy="28" r="26" fill="#c8201e" stroke="#fff" stroke-width="4"/><path d="M22 17v22l17-11z" fill="#fff"/></svg>
    <span class="arrow next"><svg width="14" height="22" viewBox="0 0 14 22"><path d="M3 2l8 9-8 9" fill="none" stroke="#fff" stroke-width="2.5"/></svg></span>
  </div>
  <h2 class="abs section-title" style="left:676px;top:723px">Tune in on Clipstream</h2>
  <p class="abs copy" style="left:679px;top:798px">Lorem ipsum dolor sit amet, consectetur adipiscing elit, sed do eiusmod tempor incididunt ut labore et dolore magn ipsum suspendisse ultrices graisus commodo viverra maecenas accumsan lacus vel facilisis. Lorem ipsum dolor sit amet, consectetur adipiscing elit</p>
  <a class="abs btn btn-wide" style="left:679px;top:969px">SUBSCRIBE ON CLIPSTREAM</a>
</section>

<section>
  <h2 class="abs section-title" style="left:144px;top:1161px">Find on Friendwall</h2>
  <p class="abs copy" style="left:149px;top:1234px">Lorem ipsum dolor sit amet, consectetur adipiscing elit, sed do eiusmod tempor incididunt ut labore et dolore magn ipsum suspendisse ultrices graisus commodo viverra maecenas accumsan lacus vel facilisis. Lorem ipsum dolor sit amet, consectetur adipiscing elit</p>
  <a class="abs btn btn-wide" style="left:149px;top:1405px">FIND ON FRIENDWALL</a>
  <div class="abs media media-dirt" style="left:594px;top:1143px" role="img" aria-label="Motocross rider cornering through dust">
    <span class="arrow prev"><svg width="14" height="22" viewBox="0 0 14 22"><path d="M11 2 3 11l8 9" fill="none" stroke="#fff" stroke-width="2.5"/></svg></span>
    <span class="arrow next"><svg width="14" height="22" viewBox="0 0 14 22"><path d="M3 2l8 9-8 9" fill="none" stroke="#fff" stroke-width="2.5"/></svg></span>
  </div>
</section>

<section>
  <div class="abs media media-curve" style="left:145px;top:1580px" role="img" aria-label="Motorcyclist riding a curved mountain road">
    <span class="arrow prev"><svg width="14" height="22" viewBox="0 0 14 22"><path d="M11 2 3 11l8 9" fill="none" stroke="#fff" stroke-width="2.5"/></svg></span>
    <span class="arrow next"><svg width="14" height="22" viewBox="0 0 14 22"><path d="M3 2l8 9-8 9" fill="none" stroke="#fff" stroke-width="2.5"/></svg></span>
  </div>
  <h2 class="abs section-title" style="left:676px;top:1598px">Find me on Snapgrid!</h2>
  <p class="abs copy" style="left:681px;top:1671px">Lorem ipsum dolor sit amet, consectetur adipiscing elit, sed do eiusmod tempor incididunt ut labore et dolore magn ipsum suspendisse ultrices graisus commodo viverra maecenas accumsan lacus vel facilisis. Lorem ipsum dolor sit amet, consectetur adipiscing elit</p>
  <a class="abs btn btn-wide" style="left:681px;top:1842px">FIND ON SNAPGRID</a>
</section>

<section class="abs newsletter"></section>
<h2 class="abs section-title newsletter-title">Newsletter sign up!</h2>
<p class="abs newsletter-lead">Sed ut perspiciatis unde omnis iste natusedoloremoloremque laudantium</p>
<div class="abs email">Enter Email</div>
<a class="abs btn btn-subscribe">SUBSCRIBE</a>

<footer class="abs footer"></footer>
<nav class="abs social">
  <a aria-label="Clipstream"></a><a aria-label="Friendwall"></a><a aria-label="Snapgrid"></a>
</nav>
<p class="abs legal">© 2022 Brintle.All Rights Reserved &nbsp;|&nbsp; Privacy &nbsp;|&nbsp; Terms of use</p>

</body>
</html>
```